Global Consulting firm needs a Business Card Design (Contest)

We need a business card design for a company with global reach called 'Harborline Group'. Harborline Group is a Trusted Procurement Advisor that consults for Zenith 400 and Meridian 900 companies to find cost reductions in their spending. We would like to see designs that communicate fiduciary trust and sense of partnership. The Front should have our logo w/ 'trusted procurement advisor', Employee name and title, company address, email, phone and fax (logo attached "Harbor line group final"). The color scheme and basic concept should be consistent with our presentation front page (attached "HLG presentation cover page"). The Back should have our website (www.hlinellc.com) and an array of our areas of expertise: office supplies, lab supplies, wireless telecom, MRO and IT (see "lab supplies" file for example).

```html
<!DOCTYPE html>
<html lang="en">
<head>
<meta charset="utf-8">
<title>Harborline Group – Business Card</title>
<link href="https://fonts.googleapis.com/css2?family=Crimson+Text:ital,wght@0,400;1,400&family=PT+Sans:wght@400;700&display=swap" rel="stylesheet">
<style>
  :root {
    --backdrop: #e9e6e1;
    --card: #ffffff;
    --ink: #1a1a1a;
    --gold: #c9941f;
    --gold-deep: #b98516;
    --map-tone: #efe6d6;
    --navy: #1f2f6b;
    --tile-office: #e9b7c9;
    --tile-lab: #dfe8ef;
    --tile-telecom: #3f74b6;
    --tile-mro: #d9dde2;
    --tile-ship: #b99266;
  }
  * { margin: 0; padding: 0; box-sizing: border-box; }
  html, body { width: 1200px; height: 1000px; overflow: hidden; }
  body { background: var(--backdrop); position: relative; font-family: "PT Sans", Arial, sans-serif; color: var(--ink); }

  .card {
    position: absolute; left: 265px; width: 665px; height: 397px;
    background: var(--card); border-radius: 22px; overflow: hidden;
    box-shadow: 0 6px 16px rgba(0,0,0,0.18);
  }
  .card--front { top: 73px; }
  .card--back { top: 533px; }

  .map-backdrop { position: absolute; left: 20px; top: 15px; width: 630px; height: 330px; }

  .brand { position: absolute; display: flex; align-items: center; }
  .brand__mark { width: 36px; height: 36px; border-radius: 50%; background: var(--gold); flex: none; }
  .brand__name {
    font-family: "Crimson Text", Georgia, serif; font-weight: 400; font-size: 35px;
    color: var(--ink); line-height: 1; margin-left: 26px; white-space: nowrap;
  }
  .card--front .brand { left: 32px; top: 37px; }
  .tagline {
    position: absolute; left: 127px; top: 77px;
    font-family: "Crimson Text", Georgia, serif; font-style: italic; font-size: 19px; color: var(--ink);
  }

  .person { position: absolute; left: 33px; top: 220px; }
  .person__name { font-weight: 700; font-size: 21px; color: var(--gold); line-height: 1.2; }
  .person__title { font-size: 19px; line-height: 1.15; }

  .divider { position: absolute; left: 33px; top: 276px; width: 600px; height: 2px; background: var(--gold); }

  .contact { position: absolute; left: 33px; top: 288px; list-style: none; }
  .contact__item { display: flex; align-items: center; height: 27px; font-size: 19px; }
  .contact__icon { width: 22px; height: 22px; margin-right: 6px; flex: none; }

  .office { position: absolute; right: 32px; top: 290px; text-align: right; }
  .office__company { font-weight: 700; font-size: 18px; color: var(--gold); letter-spacing: 0.2px; }
  .office__place { font-size: 18px; line-height: 1.35; }

  .card--back .brand { left: 150px; top: 107px; }
  .card--back .brand__mark { width: 42px; height: 42px; }
  .card--back .brand__name { margin-left: 16px; font-size: 35px; }
  .website {
    position: absolute; left: 0; width: 100%; top: 150px; padding-left: 45px; text-align: center;
    font-weight: 700; font-size: 17px; letter-spacing: 3.4px; color: var(--gold-deep);
  }

  .expertise { position: absolute; left: 46px; top: 207px; width: 580px; height: 78px; list-style: none; }
  .expertise__tile {
    position: absolute; top: 0; height: 78px;
    border: 1.5px solid var(--navy); background: #fff;
  }
  .expertise__image { position: absolute; left: 2px; top: 2px; right: 2px; bottom: 2px; }
  .expertise__label {
    position: absolute; left: 4px; top: -1px; height: 14px; padding: 0 9px;
    background: var(--navy); color: #fff; font-size: 9px; line-height: 14px;
    border-radius: 0 0 6px 0; white-space: nowrap;
  }
  .tile-office { left: 0; width: 105px; }
  .tile-office .expertise__image { background: linear-gradient(135deg, var(--tile-office), #f4e27a 55%, #9fd3ee); }
  .tile-lab { left: 117px; width: 105px; }
  .tile-lab .expertise__image { background: linear-gradient(135deg, #ffffff, var(--tile-lab) 60%, #b9d6ea); }
  .tile-telecom { left: 237px; width: 105px; }
  .tile-telecom .expertise__image { background: radial-gradient(circle at 40% 60%, #8fb8e6, var(--tile-telecom) 70%, #1f4e8f); }
  .tile-mro { left: 358px; width: 99px; }
  .tile-mro .expertise__image { background: linear-gradient(135deg, #ffffff, var(--tile-mro) 60%, #aeb5bd); }
  .tile-ship { left: 469px; width: 105px; }
  .tile-ship .expertise__image { background: linear-gradient(135deg, #d7b88e, var(--tile-ship) 60%, #8a6a45); }
</style>
</head>
<body>

  <section class="card card--front" aria-label="Business card front">
    <svg class="map-backdrop" role="img" aria-label="Faint world map backdrop" viewBox="0 0 630 330">
      <defs>
        <radialGradient id="mapFront" cx="55%" cy="45%" r="60%">
          <stop offset="0%" stop-color="#efe6d6" stop-opacity="0.75"/>
          <stop offset="100%" stop-color="#efe6d6" stop-opacity="0.15"/>
        </radialGradient>
      </defs>
      <rect x="0" y="0" width="630" height="330" rx="30" fill="url(#mapFront)"/>
    </svg>

    <div class="brand">
      <span class="brand__mark" aria-hidden="true"></span>
      <span class="brand__name">Harborline Group</span>
    </div>
    <p class="tagline">Trusted Procurement Advisor</p>

    <div class="person">
      <p class="person__name">Daniel Whitcombe</p>
      <p class="person__title">Manager</p>
    </div>

    <div class="divider"></div>

    <ul class="contact">
      <li class="contact__item">
        <svg class="contact__icon" viewBox="0 0 22 22" aria-label="Phone">
          <circle cx="11" cy="11" r="10" fill="none" stroke="#c9941f" stroke-width="1.6"/>
          <path d="M6 9.5c0-2 2-3 5-3s5 1 5 3v1h-2.5V9h-5v1.5H6z" fill="#c9941f"/>
          <rect x="7" y="11" width="8" height="5" rx="1" fill="#c9941f"/>
        </svg>
        866 - 555 - 0142
      </li>
      <li class="contact__item">
        <svg class="contact__icon" viewBox="0 0 22 22" aria-label="Fax">
          <circle cx="11" cy="11" r="10" fill="none" stroke="#c9941f" stroke-width="1.6"/>
          <rect x="8" y="5.5" width="6" height="4" fill="#c9941f"/>
          <rect x="5.5" y="9.5" width="11" height="5" rx="1" fill="#c9941f"/>
          <rect x="8" y="13" width="6" height="3.5" fill="#fff" stroke="#c9941f" stroke-width="1"/>
        </svg>
        609 - 555 - 0187
      </li>
      <li class="contact__item">
        <svg class="contact__icon" viewBox="0 0 22 22" aria-label="Email">
          <circle cx="11" cy="11" r="10" fill="none" stroke="#c9941f" stroke-width="1.6"/>
          <rect x="5.5" y="7" width="11" height="8" fill="#c9941f"/>
          <path d="M5.5 7l5.5 4.5L16.5 7" fill="none" stroke="#fff" stroke-width="1"/>
        </svg>
        info@hlinellc.com
      </li>
    </ul>

    <div class="office">
      <p class="office__company">HARBORLINE GROUP</p>
      <p class="office__place">Oak Harbor, New Jersey</p>
    </div>
  </section>

  <section class="card card--back" aria-label="Business card back">
    <svg class="map-backdrop" role="img" aria-label="Faint world map backdrop" viewBox="0 0 630 330">
      <defs>
        <radialGradient id="mapBack" cx="55%" cy="40%" r="60%">
          <stop offset="0%" stop-color="#efe6d6" stop-opacity="0.75"/>
          <stop offset="100%" stop-color="#efe6d6" stop-opacity="0.15"/>
        </radialGradient>
      </defs>
      <rect x="0" y="0" width="630" height="330" rx="30" fill="url(#mapBack)"/>
    </svg>

    <div class="brand">
      <span class="brand__mark" aria-hidden="true"></span>
      <span class="brand__name">Harborline Group</span>
    </div>
    <p class="website">www.hlinellc.com</p>

    <ul class="expertise">
      <li class="expertise__tile tile-office">
        <div class="expertise__image" role="img" aria-label="Photo of sticky notes, paper clips and pens"></div>
        <span class="expertise__label">Office Supplies</span>
      </li>
      <li class="expertise__tile tile-lab">
        <div class="expertise__image" role="img" aria-label="Photo of laboratory test tubes and glassware"></div>
        <span class="expertise__label">Lab Supplies</span>
      </li>
      <li class="expertise__tile tile-telecom">
        <div class="expertise__image" role="img" aria-label="Photo of a mobile phone held before a globe"></div>
        <span class="expertise__label">Wireless Telecom</span>
      </li>
      <li class="expertise__tile tile-mro">
        <div class="expertise__image" role="img" aria-label="Photo of a wrench on a nut"></div>
        <span class="expertise__label">MRO</span>
      </li>
      <li class="expertise__tile tile-ship">
        <div class="expertise__image" role="img" aria-label="Photo of a handheld scanner reading a parcel label"></div>
        <span class="expertise__label">Shipping/Postage</span>
      </li>
    </ul>
  </section>

</body>
</html>
```